Corporate Branded Documents - IT Provider - On-going work

Hi, I'm Ned a Director of Harbourlane ICT Support a UK Based IT & Telecoms support firm. We've been trading for 12 years now and feel its time for a lick of paint. We have a logo, website etc but would like someone to create some standard documents for us.

- A PDF Proposal Template - We currently don't send our customers proposals as we have nothing that looks good.
- A Quote Template PDF - Example Attached
- A Order Template PDF - Example Attached
- A Invoice Template PDF - Example Attached
- A Generic Document PDF - Something we can use for customer application forms, NDA Agreements, Terms & Conditions etc

Our website can be found at www.harbourlaneictsupport.co.uk - here you'll get a feel for our branding. I've also attached 2 example documents - as well as our currently used documents. Hopefully you guys can see why it needs improving.

We'd also like to work with someone long term, these documents are a start but we'd like to make sure all the work we do looks and feels as smart as possible, so there is plenty of additional work available.

None of these templates need to be Print ready, 99% of the time it will be viewed digitally, so high resolution designs are best

Thanks,

Ned

Target Market(s)

Corporate & Educational Customers

Industry/Entity Type

It Support

Font styles to use
Sans Serif

Colors
ec1f27
0692cd
ffffff

```html
<!DOCTYPE html>
<html lang="en">
<head>
<meta charset="utf-8">
<title>Harbourlane ICT Support – Proposal Cover</title>
<link rel="stylesheet" href="https://fonts.googleapis.com/css2?family=Montserrat:wght@400;600;700&family=Arimo:wght@400;700&display=swap">
<style>
  :root {
    --brand-red: #cc1719;
    --brand-teal: #0a8199;
    --brand-teal-deep: #087a91;
    --brand-sky: #3bbfe0;
    --ribbon-shadow: #d9d9d9;
    --paper: #ffffff;
    --rule: rgba(255, 255, 255, 0.45);
  }
  * { margin: 0; padding: 0; box-sizing: border-box; }
  html, body {
    width: 843px;
    height: 1200px;
    overflow: hidden;
    background: var(--paper);
  }
  .cover {
    position: relative;
    width: 843px;
    height: 1200px;
    overflow: hidden;
    background: var(--paper);
    font-family: "Montserrat", Arial, sans-serif;
  }
  .cover-shapes {
    position: absolute;
    inset: 0;
    width: 843px;
    height: 1200px;
  }
  .ribbon-meta {
    position: absolute;
    left: 48px;
    width: 350px;
    text-align: center;
    color: var(--paper);
    font-family: "Montserrat", Arial, sans-serif;
    font-weight: 400;
    font-size: 24px;
    letter-spacing: 0.3px;
  }
  .ribbon-meta--date { top: 263px; }
  .ribbon-meta--presenter { top: 318px; }

  .brand-name {
    position: absolute;
    left: 428px;
    width: 390px;
    top: 155px;
    text-align: center;
    font-family: "Montserrat", Arial, sans-serif;
    font-weight: 600;
    font-size: 28px;
    line-height: 34px;
    color: var(--brand-teal);
    white-space: nowrap;
  }

  .cover-title {
    position: absolute;
    left: 0;
    width: 843px;
    top: 790px;
    text-align: center;
    color: var(--paper);
    font-family: "Montserrat", Arial, sans-serif;
    font-weight: 700;
    font-size: 41px;
    letter-spacing: 0.4px;
  }
  .cover-subtext {
    position: absolute;
    left: 150px;
    width: 543px;
    top: 877px;
    text-align: center;
    color: var(--paper);
    font-family: "Arimo", Arial, sans-serif;
    font-size: 20px;
    line-height: 34px;
  }
  .cover-rule {
    position: absolute;
    left: 160px;
    width: 522px;
    top: 957px;
    height: 2px;
    background: var(--rule);
  }
  .cover-name {
    position: absolute;
    left: 0;
    width: 843px;
    top: 990px;
    text-align: center;
    color: var(--paper);
    font-family: "Arimo", Arial, sans-serif;
    font-weight: 700;
    font-size: 28px;
    letter-spacing: 0.6px;
  }
</style>
</head>
<body>
<main class="cover">
  <svg class="cover-shapes" viewBox="0 0 843 1200" aria-hidden="true">
    <polygon class="band-accent" points="0,448 843,393 843,1200 0,1200" fill="var(--brand-sky)"/>
    <polygon class="band-main" points="0,459 843,404 843,1200 0,1200" fill="var(--brand-teal)"/>
    <polygon class="band-shade" points="140,560 843,470 843,1200 170,1200" fill="var(--brand-teal-deep)" opacity="0.5"/>
    <polygon class="ribbon-shadow" points="36,553 398,485 398,497 36,565" fill="var(--ribbon-shadow)"/>
    <polygon class="ribbon" points="48,0 398,0 398,485 36,553" fill="var(--brand-red)"/>
  </svg>

  <p class="ribbon-meta ribbon-meta--date">JULY 2018</p>
  <p class="ribbon-meta ribbon-meta--presenter">PERSENTATOR NAME</p>

  <p class="brand-name">Harbourlane ICT Support</p>

  <h1 class="cover-title">PERSENTATION TITLE HERE</h1>
  <p class="cover-subtext">Subtext here Subtext here Subtext here Subtext here Subtext here Subtext here</p>
  <div class="cover-rule"></div>
  <p class="cover-name">Persentation Name</p>
</main>
</body>
</html>
```